A paperback book cover entitled: The Keystone

1. For the front cover of the paperback I need the photo of me walking down the driveway at Wexcombe Hall as the focal point. The designer will use their discretion where to insert the book title: The Keystone.
Also the designer will use their discretion where my name Desmond Harrowby as the author is placed. Attached is a contemporary photo of me to use if the designer thinks that possible. Both these photos are attached.
2. The back cover page will contain two main written insertions (1) About the Book and (2) About the Author.
The book will be an 8.5x11 inch paperback of some 570 pages published by Brindlepress.
About the book:
This book is about Australian Public Affairs 1957-2020 as perceived and observed by Desmond Harrowby. It has a significant but not exclusive Queensland focus concerning History, Commentary, and Anecdotes, plus some things Desmond has been involved with along the way.
Desmond developed unique Transition to Government and Transition to Opposition plans that have all been implemented. Some of those plans are referred to in the book and other Transition plans are appendixes to the book.
Now at 73 years of age, Desmond’s motivation for writing this book is to ensure a wealth of historical scenarios are captured and incorporated into the public record for future generations.

About the author:

Desmond Harrowby has been a largely silent and invisible political confidant to Australian Premiers and Prime Ministers.
Desmond worked in the Queensland public sector from 1971-2009 as Chief of Staff to four Queensland State Opposition Leaders for 13 years and then as a Public Sector senior executive.
He subsequently served on the Edith Tarrant Foundation Board, the Orrin Vale Records Hall Board, and consulted to a mining company. He has recorded many Oral History projects for The Fernwick Archive in Canberra.
Over the last 30+ years, he has been approached countless times for advice relating to Business, Government, Authors, Historians, and people seeking a job. He has never charged a cent for any of his advice, even when not working within Government.
There are two extra photos attached to maybe be on each side at the bottom of the back cover if the designer thinks it is appropriate.
Those in the 4 person photo from the left were all connected with the Tallowmere Assembly: former Unity Minister Neil Corrigan, Former Heartland Party Premier Tom Beaulieu, former Progress Leader Glen Osborne, and Desmond Harrowby

In the three person photo from the left are: Desmond Harrowby, Former PM Rupert Danforth, and Prime Minister Brian Ferrow.

3. In the spine of the book will be simply (1) The Keystone and (2) Desmond Harrowby

Here’s hoping a good design is created.

```html
<!DOCTYPE html>
<html lang="en">
<head>
<meta charset="utf-8">
<title>The Keystone – Cover Spread</title>
<link rel="stylesheet" href="https://fonts.googleapis.com/css2?family=Libre+Baskerville:wght@400;700&family=Source+Sans+3:wght@400;600&display=swap">
<style>
  :root {
    --page-bg: #ececec;
    --back-cover: #d8cfbb;
    --ink-dark: #3a3427;
    --title-cream: #ece3cc;
    --body-ink: #2e2a22;
    --photo-light: #b9b3a6;
    --photo-mid: #8d877b;
    --photo-dark: #4d483f;
  }
  * { margin: 0; padding: 0; box-sizing: border-box; }
  html, body { width: 800px; height: 1200px; overflow: hidden; }
  body { background: var(--page-bg); position: relative; }

  .cover-spread {
    position: absolute; left: 20px; top: 310px;
    width: 760px; height: 580px;
    display: flex;
    box-shadow: 0 6px 18px rgba(0,0,0,0.18);
  }

  /* Back cover */
  .back-cover {
    width: 380px; height: 100%;
    background: var(--back-cover);
    padding: 22px 22px 18px;
    position: relative;
    color: var(--body-ink);
    font-family: "Source Sans 3", Arial, sans-serif;
  }
  .back-title {
    font-family: "Libre Baskerville", Georgia, serif;
    font-weight: 700; color: var(--ink-dark);
    line-height: 0.95; margin-bottom: 14px;
  }
  .back-title .title-article { display: block; font-size: 13px; }
  .back-title .title-main { display: block; font-size: 28px; }
  .section-heading {
    font-family: "Libre Baskerville", Georgia, serif;
    font-weight: 700; font-size: 12.5px; color: var(--ink-dark);
    margin: 0 0 4px;
  }
  .body-copy { font-size: 7.4px; line-height: 1.38; margin-bottom: 4px; text-align: justify; }
  .about-book { margin-bottom: 10px; }
  .author-row { display: flex; gap: 9px; align-items: flex-start; }
  .author-portrait {
    width: 64px; height: 78px; flex: none;
    background: linear-gradient(160deg, var(--photo-light), var(--photo-mid));
  }
  .author-row .body-copy { flex: 1; }

  .back-photos {
    position: absolute; left: 22px; bottom: 22px;
    display: flex; gap: 10px;
  }
  .group-photo { height: 72px; }
  .group-photo.four-person { width: 108px; background: linear-gradient(180deg, var(--photo-light), var(--photo-mid)); }
  .group-photo.three-person { width: 100px; background: linear-gradient(180deg, #c4bfb4, var(--photo-mid)); }

  /* Spine */
  .spine {
    width: 40px; height: 100%;
    background: var(--ink-dark);
    display: flex; align-items: flex-start; justify-content: center;
    padding-top: 26px;
  }
  .spine-author {
    writing-mode: vertical-rl;
    font-family: "Libre Baskerville", Georgia, serif;
    font-size: 11px; letter-spacing: 0.5px;
    color: var(--title-cream);
  }

  /* Front cover */
  .front-cover { width: 340px; height: 100%; display: flex; }
  .title-band {
    width: 118px; height: 100%;
    background: var(--ink-dark);
    display: flex; justify-content: center; padding-top: 24px;
  }
  .front-title {
    writing-mode: vertical-rl;
    font-family: "Libre Baskerville", Georgia, serif;
    font-weight: 700; color: var(--title-cream);
    line-height: 0.9;
  }
  .front-title .title-article { font-size: 34px; }
  .front-title .title-main { font-size: 64px; }
  .cover-photo {
    flex: 1; height: 100%;
    background:
      radial-gradient(ellipse at 55% 55%, rgba(40,36,30,0.55), transparent 45%),
      linear-gradient(180deg, var(--photo-mid) 0%, var(--photo-light) 45%, #cfc9bc 75%, var(--photo-mid) 100%);
  }
</style>
</head>
<body>
  <div class="cover-spread">
    <section class="back-cover">
      <h1 class="back-title">
        <span class="title-article">The</span>
        <span class="title-main">Keystone</span>
      </h1>

      <div class="about-book">
        <h2 class="section-heading">About the book:</h2>
        <p class="body-copy">This book is about Australian Public Affairs 1957-2020 as perceived and observed by Desmond Harrowby. It has a significant but not exclusive Queensland focus concerning History, Commentary, and Anecdotes, plus some things Desmond has been involved with along the way.</p>
        <p class="body-copy">Desmond developed unique Transition to Government and Transition to Opposition plans that have all been implemented. Some of those plans are referred to in the book and other Transition plans are appendixes to the book.</p>
        <p class="body-copy">Now at 73 years of age, Desmond’s motivation for writing this book is to ensure a wealth of historical scenarios are captured and incorporated into the public record for future generations.</p>
      </div>

      <div class="about-author">
        <h2 class="section-heading">About the author:</h2>
        <div class="author-row">
          <div class="author-portrait" role="img" aria-label="Portrait photograph of the author Desmond Harrowby"></div>
          <div class="body-copy">
            <p class="body-copy">Desmond Harrowby has been a largely silent and invisible political confidant to Australian Premiers and Prime Ministers.</p>
            <p class="body-copy">Desmond worked in the Queensland public sector from 1971-2009 as Chief of Staff to four Queensland State Opposition Leaders for 13 years and then as a Public Sector senior executive.</p>
          </div>
        </div>
        <p class="body-copy">He subsequently served on the Edith Tarrant Foundation Board, the Orrin Vale Records Hall Board, and consulted to a mining company. He has recorded many Oral History projects for The Fernwick Archive in Canberra.</p>
        <p class="body-copy">Over the last 30+ years, he has been approached countless times for advice relating to Business, Government, Authors, Historians, and people seeking a job. He has never charged a cent for any of his advice, even when not working within Government.</p>
      </div>

      <div class="back-photos">
        <div class="group-photo four-person" role="img" aria-label="Photograph of Neil Corrigan, Tom Beaulieu, Glen Osborne and Desmond Harrowby"></div>
        <div class="group-photo three-person" role="img" aria-label="Photograph of Desmond Harrowby, Rupert Danforth and Brian Ferrow"></div>
      </div>
    </section>

    <section class="spine">
      <span class="spine-author">Desmond Harrowby</span>
    </section>

    <section class="front-cover">
      <div class="title-band">
        <h2 class="front-title"><span class="title-article">The </span><span class="title-main">Keystone</span></h2>
      </div>
      <div class="cover-photo" role="img" aria-label="Sepia photograph of the author walking down the driveway at Wexcombe Hall"></div>
    </section>
  </div>
</body>
</html>
```